Business card alterations

I have changed my business name from Brisa Laser Renewal Clinic to simply "Brisa Laser Clinic' and need this logo changed to reflect same

Brisa Laser Clinic
Est. 2004

I also need new business cards with above logo included and this attached card changed to the following.
Marianne Holcroft
Dermal Aesthetician
Grad Cert in Laser & IPL Treatments

I need at least one logo in less than 4mb so I can upload into my newsletter format so I can upload to newsletters, emails etc

Thanks
Mari

```html
<!DOCTYPE html>
<html lang="en">
<head>
<meta charset="utf-8">
<title>Brisa Laser Clinic – Business Card</title>
<link rel="stylesheet" href="https://fonts.googleapis.com/css2?family=Noto+Serif:wght@400;700&display=swap">
<style>
  :root {
    --page-bg: #e6e6e8;
    --card-green: #00a05e;
    --band-grey: #c9c9c9;
    --band-dark: #2b2728;
    --email-green: #17995a;
    --text-white: #ffffff;
  }
  * { margin: 0; padding: 0; box-sizing: border-box; }
  html, body {
    width: 1200px; height: 864px; overflow: hidden;
    background: var(--page-bg);
    font-family: "Noto Serif", Georgia, serif;
  }
  .card {
    position: absolute; left: 100px; top: 146px;
    width: 1000px; height: 572px;
    background: var(--card-green);
    color: var(--text-white);
    overflow: hidden;
    box-shadow: 0 18px 40px rgba(0,0,0,.18);
  }
  .holder { position: absolute; left: 70px; top: 100px; }
  .holder-name { font-weight: 700; font-size: 38px; line-height: 1.1; }
  .holder-role { font-size: 22px; margin-top: 4px; }

  .brand { position: absolute; right: 80px; top: 34px; text-align: center; width: 340px; }
  .brand-name { font-size: 112px; line-height: 1; font-weight: 400; letter-spacing: -1px; }
  .brand-line { font-size: 26px; font-variant: small-caps; letter-spacing: 5px; margin-top: 14px; line-height: 1.15; }

  .band-grey {
    position: absolute; left: 0; top: 284px; width: 560px; height: 30px;
    background: var(--band-grey);
    clip-path: polygon(0 0, 97% 0, 100% 100%, 0 100%);
  }
  .email { position: absolute; left: 64px; top: 286px; font-size: 21px; color: var(--email-green); }
  .band-dark {
    position: absolute; left: 546px; top: 254px; right: 0; height: 34px;
    background: var(--band-dark);
    clip-path: polygon(0 0, 100% 0, 100% 100%, 3% 100%);
  }
  .phone { position: absolute; left: 640px; top: 256px; font-size: 22px; }

  .credential { position: absolute; left: 64px; top: 354px; font-size: 27px; }

  .contact { position: absolute; left: 70px; top: 450px; font-size: 22px; list-style: none; }
  .contact li { display: flex; align-items: center; gap: 22px; height: 38px; }
  .contact svg { width: 26px; height: 24px; fill: var(--text-white); }
</style>
</head>
<body>
  <article class="card">
    <div class="holder">
      <h1 class="holder-name">Marianne Holcroft</h1>
      <p class="holder-role">Dermal Aesthetician</p>
    </div>

    <div class="brand">
      <div class="brand-name">Brisa</div>
      <div class="brand-line">Brisa Laser Clinic<br>Est. 2004</div>
    </div>

    <div class="band-dark"></div>
    <p class="phone">(08) 8124 5307</p>

    <div class="band-grey"></div>
    <p class="email">info@brisaclinic.com.au</p>

    <p class="credential">Grad Cert in Laser &amp; IPL Treatments</p>

    <ul class="contact">
      <li>
        <svg viewBox="0 0 26 24" aria-hidden="true"><path d="M2 2h22v14H2z M5 5v8h16V5z M10 18h6v2h4v2H6v-2h4z" fill-rule="evenodd"/></svg>
        <span>www.brisaclinic.com.au</span>
      </li>
      <li>
        <svg viewBox="0 0 26 24" aria-hidden="true"><path d="M13 2 1 13h4v9h6v-6h4v6h6v-9h4z"/></svg>
        <span>58 Wattle Grove Road Kensington SA 5068</span>
      </li>
    </ul>
  </article>
</body>
</html>
```